High Tech Real Estate Startup needs a business card

We are developing an innovative real estate marketing product based around advanced search and virtual reality.

We talk to people, we need business cards.

Target Market(s)

The target market is technology professionals and realtors.

Contact Information for Business Card

The information to be included will include

Name
Title
Phone Number
E-mail Address
www.zelquin.com

It should use simple iconography for each one of those fields.

Font styles to use
Other font styles liked:
• Co, Jubilat, Avenir

Colors

Designer to choose colors to be used in the design.

Requirements
Must have
• Clean aesthetic,
• Good use of negative space.
• It should use our company logo, shown in the attached file. It is able to use the negative of that logo (coloured font and white background) and I have attached other acceptable accent colours in a swatch file.
Should not have
• Should not be too busy
• No extraneous text (slogans, tag lines etc)

```html
<!DOCTYPE html>
<html lang="en">
<head>
<meta charset="utf-8">
<title>Zelquin business card</title>
<link href="https://fonts.googleapis.com/css2?family=Mulish:wght@400;500;600&display=swap" rel="stylesheet">
<style>
  :root {
    --teal: #13b2b6;
    --ink: #3f5561;
    --card: #ffffff;
    --backdrop: #e8e5de;
  }
  * { margin: 0; padding: 0; box-sizing: border-box; }
  html, body { width: 1200px; height: 1000px; overflow: hidden; }
  body {
    position: relative;
    background: var(--backdrop);
    font-family: "Mulish", "Avenir", sans-serif;
    color: var(--ink);
  }
  .card {
    position: absolute;
    left: 270px;
    width: 658px;
    height: 375px;
    background: var(--card);
    box-shadow: 0 6px 18px rgba(0, 0, 0, 0.12);
    overflow: hidden;
  }
  .card-front { top: 78px; }
  .card-back { top: 534px; }

  .front-wordmark {
    position: absolute;
    top: 128px;
    left: 0;
    width: 100%;
    text-align: center;
    font-size: 80px;
    font-weight: 500;
    letter-spacing: 2px;
    line-height: 1;
    color: var(--teal);
  }

  .person-name {
    position: absolute;
    left: 46px;
    top: 122px;
    font-size: 33px;
    font-weight: 400;
    line-height: 1;
  }
  .person-title {
    position: absolute;
    left: 47px;
    top: 168px;
    font-size: 18px;
    line-height: 1;
  }
  .accent {
    position: absolute;
    left: 0;
    top: 0;
  }
  .back-wordmark {
    position: absolute;
    left: 424px;
    top: 134px;
    width: 194px;
    text-align: center;
    font-size: 44px;
    font-weight: 600;
    letter-spacing: 1px;
    line-height: 1;
    color: var(--teal);
  }
  .website {
    position: absolute;
    left: 408px;
    top: 189px;
    width: 250px;
    text-align: center;
    font-size: 19px;
    font-weight: 500;
    letter-spacing: 0.5px;
    line-height: 1;
    color: #ffffff;
  }
  .contact-list {
    position: absolute;
    left: 46px;
    top: 246px;
    list-style: none;
  }
  .contact-item {
    display: flex;
    align-items: center;
    height: 37px;
    font-size: 21px;
  }
  .contact-icon {
    width: 18px;
    height: 18px;
    margin-right: 22px;
    fill: var(--ink);
  }
</style>
</head>
<body>
  <section class="card card-front">
    <div class="front-wordmark">ZELQUIN</div>
  </section>

  <section class="card card-back">
    <div class="person-name">Name of Person</div>
    <div class="person-title">Title of Person</div>

    <svg class="accent" width="658" height="375" viewBox="0 0 658 375" aria-hidden="true">
      <line x1="196" y1="183" x2="410" y2="183" stroke="var(--teal)" stroke-width="2"/>
      <path d="M408 182 H658 V219 H432 Q416 219 412 204 Z" fill="var(--teal)"/>
    </svg>

    <div class="back-wordmark">ZELQUIN</div>
    <div class="website">www.zelquin.com</div>

    <ul class="contact-list">
      <li class="contact-item">
        <svg class="contact-icon" viewBox="0 0 24 24" aria-hidden="true">
          <path d="M6.6 10.8a15.2 15.2 0 0 0 6.6 6.6l2.2-2.2c.3-.3.7-.4 1-.2 1.1.4 2.3.6 3.6.6.6 0 1 .4 1 1V20c0 .6-.4 1-1 1C10.6 21 3 13.4 3 4c0-.6.4-1 1-1h3.5c.6 0 1 .4 1 1 0 1.3.2 2.5.6 3.6.1.3 0 .7-.2 1z"/>
        </svg>
        <span>+123 456 7890</span>
      </li>
      <li class="contact-item">
        <svg class="contact-icon" viewBox="0 0 24 24" aria-hidden="true">
          <path d="M2 6h20v1.2l-10 6.3L2 7.2z M2 9.4l10 6.3 10-6.3V18H2z"/>
        </svg>
        <span>E-mail Address</span>
      </li>
    </ul>
  </section>
</body>
</html>
```